Business Card for a Jewellery Brand

Business card for an upscale jewellery brand. Attached is the brand logo and icon and color board. I am looking for two card versions: one for the founder and one is generic. The card should be elegant and convey upscale and premium feel. I am open to both square and rectangle card shapes.

Industry/Entity Type

Jewelry

Contact Information for Business Card

Two cards: (1) Sunela Parvaniya (Founder) (2) General
(1) Sunela Parvaniya card should have Name: Sunela Parvaniya, Title: Founder Email id: sunela@quiremo.com.au. Phone no: +61452913307
(2) Generic card should have Email id: info@quiremo.com.au. Phone no: +61436207518

Requirements
Must have
• Workmark
• ICON
• Phone no
• Email ID
• ABN: 58219740312 (Note: ABN is Business number in Australia)
• Website: www.quiremo.com.au
• Instagram: quiremo_jewellery
• Facebook: @quiremojewellery
Nice to have
• Tagline

```html
<!DOCTYPE html>
<html lang="en">
<head>
<meta charset="utf-8">
<title>Quiremo Business Cards</title>
<link href="https://fonts.googleapis.com/css2?family=Montserrat:wght@500;600&family=Lato:wght@400;700&display=swap" rel="stylesheet">
<style>
  :root {
    --backdrop: #565656;
    --card: #ffffff;
    --copper: #b26a45;
    --copper-dark: #8e4f2e;
    --ink: #2b2b2b;
    --marble-light: #f3f4f4;
    --marble-mid: #e2e4e5;
  }
  * { margin: 0; padding: 0; box-sizing: border-box; }
  html, body {
    width: 1200px; height: 900px; overflow: hidden;
    background: var(--backdrop);
  }
  .canvas { position: relative; width: 1200px; height: 900px; }
  .card {
    position: absolute; top: 238px; width: 400px; height: 400px;
    background: var(--card);
  }
  .card--front { left: 192px; }
  .card--back { left: 636px; }

  .person-name {
    position: absolute; left: 38px; top: 43px;
    font-family: "Montserrat", sans-serif; font-weight: 600;
    font-size: 21px; color: var(--copper); letter-spacing: 0.2px;
  }
  .person-title {
    position: absolute; left: 38px; top: 73px;
    font-family: "Lato", sans-serif; font-size: 17px; color: var(--ink);
  }
  .contact-list {
    position: absolute; left: 36px; top: 254px; list-style: none;
    font-family: "Lato", sans-serif; font-size: 17px; color: var(--ink);
  }
  .contact-list li { display: flex; align-items: center; height: 23.5px; }
  .contact-icon { width: 13px; height: 13px; margin-right: 6px; fill: var(--copper); }
  .business-number {
    position: absolute; left: 36px; top: 340px;
    font-family: "Lato", sans-serif; font-size: 17px; color: var(--ink);
  }
  .business-number strong { color: var(--copper); font-weight: 700; }

  .marble-surface {
    position: absolute; inset: 0;
    background: linear-gradient(135deg, var(--marble-light) 0%, var(--marble-mid) 50%, var(--marble-light) 100%);
  }
  .brand-mark {
    position: absolute; left: 0; right: 0; top: 178px; text-align: center;
    font-family: "Montserrat", sans-serif; font-weight: 500;
    font-size: 40px; letter-spacing: 10px; color: var(--copper);
  }
  .social-row { position: absolute; left: 0; top: 263px; width: 400px; height: 24px; }
  .social-handle {
    position: absolute; left: 0; right: 0; top: 300px; text-align: center;
    font-family: "Lato", sans-serif; font-size: 17px; color: var(--copper);
  }
</style>
</head>
<body>
<main class="canvas">
  <section class="card card--front">
    <h1 class="person-name">SUNELA PARVANIYA</h1>
    <p class="person-title">Founder</p>
    <ul class="contact-list">
      <li>
        <svg class="contact-icon" viewBox="0 0 16 16" aria-hidden="true"><path d="M3.5 1l2.5 3-1.5 2c.8 2 2.5 3.7 4.5 4.5l2-1.5 3 2.5-1.5 2.5C7 14 2 9 1 2.5z"/></svg>
        +61452913307
      </li>
      <li>
        <svg class="contact-icon" viewBox="0 0 16 16" aria-hidden="true"><path d="M1 3h14v10H1z M1.5 3.5L8 9l6.5-5.5" stroke="#fff" stroke-width="1"/></svg>
        sunela@quiremo.com.au.
      </li>
      <li>
        <svg class="contact-icon" viewBox="0 0 16 16" aria-hidden="true"><circle cx="8" cy="8" r="7"/><path d="M1 8h14M8 1c3 3 3 11 0 14M8 1c-3 3-3 11 0 14" stroke="#fff" stroke-width="1" fill="none"/></svg>
        www.quiremo.com.au
      </li>
    </ul>
    <p class="business-number"><strong>ABN:</strong> 58219740312</p>
  </section>

  <section class="card card--back">
    <div class="marble-surface" role="img" aria-label="White marble texture with grey veins"></div>
    <div class="brand-mark">QUIREMO</div>
    <svg class="social-row" viewBox="0 0 400 24" aria-hidden="true">
      <line x1="40" y1="12" x2="154" y2="12" stroke="var(--copper)" stroke-width="1"/>
      <circle cx="177" cy="12" r="12" fill="var(--copper)"/>
      <circle cx="213" cy="12" r="12" fill="var(--copper)"/>
      <line x1="236" y1="12" x2="360" y2="12" stroke="var(--copper)" stroke-width="1"/>
    </svg>
    <p class="social-handle">@quiremojewellery</p>
  </section>
</main>
</body>
</html>
```